Heritage Hollow Business Cards

Require a business card design. <br/><br/>Needs to include logo (either round or long version) plus these details:<br/>Maya Torvell<br/>Heritage Hollow<br/>maya@kelvadtrading.com.au<br/>02 6481 7395<br/>PO Box Glenwarra NSW 2791<br/>www.heritagehollow.com.au<br/><br/>I need in an editable format so that I can create for multiple staff members. <br/><br/>

Target Market(s)

We are an online store selling renovation products to home owners are builders. Looking for a classic classy design.

Industry/Entity Type

Home And Garden

Contact Information for Business Card

Maya Torvell
Heritage Hollow
maya@kelvadtrading.com.au
02 6481 7395
PO Box Glenwarra NSW 2791
www.heritagehollow.com.au

Colors

Designer to choose colors to be used in the design.

Requirements
Must have
• Must include Logo.

```html
<!DOCTYPE html>
<html lang="en">
<head>
<meta charset="utf-8">
<title>Heritage Hollow Business Cards</title>
<link rel="stylesheet" href="https://fonts.googleapis.com/css2?family=Work+Sans:wght@400;500;600;700&display=swap">
<style>
  :root {
    --backdrop: #e4e4e4;
    --card: #ffffff;
    --ink: #1d1d1d;
    --muted: #5c5c5c;
    --rule: #7a7a7a;
    --band: #222222;
  }
  * { margin: 0; padding: 0; box-sizing: border-box; }
  html, body {
    width: 1200px; height: 1001px; overflow: hidden;
    background: var(--backdrop);
    font-family: "Work Sans", Arial, sans-serif;
    color: var(--ink);
  }
  .stage { position: relative; width: 1200px; height: 1001px; }
  .card {
    position: absolute; left: 306px; width: 588px; height: 336px;
    background: var(--card);
    box-shadow: 0 1px 3px rgba(0,0,0,0.12);
    overflow: hidden;
  }
  .card--front { top: 135px; }
  .card--back { top: 523px; }

  .name-marker { position: absolute; left: 0; top: 94px; width: 14px; height: 44px; background: var(--band); }
  .holder { position: absolute; left: 33px; top: 93px; }
  .holder__name { font-size: 24px; font-weight: 700; letter-spacing: 1.2px; line-height: 28px; }
  .holder__role { font-size: 14px; color: var(--muted); margin-top: 2px; }

  .brand-mark {
    position: absolute; border: 1px solid var(--rule); border-radius: 50%;
    display: flex; align-items: center; justify-content: center; text-align: center;
    font-weight: 500; color: var(--ink); line-height: 1.1;
  }
  .card--front .brand-mark { left: 390px; top: 37px; width: 150px; height: 150px; font-size: 21px; }
  .card--back .brand-mark { left: 192px; top: 42px; width: 216px; height: 216px; font-size: 30px; }

  .address { position: absolute; left: 33px; top: 241px; font-size: 14px; line-height: 20px; color: var(--muted); }
  .address__company { color: var(--ink); margin-bottom: 3px; }
  .divider { position: absolute; left: 242px; top: 242px; width: 1px; height: 57px; background: var(--muted); }

  .contacts { position: absolute; left: 306px; top: 244px; list-style: none; font-size: 14px; line-height: 20px; color: var(--muted); }
  .contacts li { display: flex; align-items: center; gap: 7px; }
  .contacts svg { width: 11px; height: 11px; fill: none; stroke: var(--ink); stroke-width: 1.4; }
  .contacts strong { color: var(--ink); font-weight: 500; }

  .base-band { position: absolute; left: 0; bottom: 0; width: 588px; height: 11px; }

  .web-line { position: absolute; left: 32px; right: 32px; top: 287px; display: flex; align-items: center; gap: 10px; }
  .web-line__rule { flex: 1; height: 1px; background: var(--ink); }
  .web-line__url { font-size: 14px; letter-spacing: 3px; }
  .web-line__url strong { font-weight: 600; }
</style>
</head>
<body>
<main class="stage">
  <section class="card card--front" aria-label="Business card front">
    <div class="name-marker"></div>
    <div class="holder">
      <p class="holder__name">Maya Torvell</p>
      <p class="holder__role">Director</p>
    </div>
    <div class="brand-mark">Heritage<br>Hollow</div>

    <div class="address">
      <p class="address__company">Heritage Hollow</p>
      <p>PO Box Glenwarra</p>
      <p>NSW 2791</p>
    </div>
    <div class="divider"></div>
    <ul class="contacts">
      <li><svg viewBox="0 0 12 12"><path d="M2 1.5l2 0 1 2.5-1.3 1a6 6 0 0 0 3.3 3.3l1-1.3 2.5 1v2a1 1 0 0 1-1 1A9 9 0 0 1 1 2.5a1 1 0 0 1 1-1z"/></svg>02 6481 7395</li>
      <li><svg viewBox="0 0 12 12"><rect x="1" y="2.5" width="10" height="7"/><path d="M1 2.5l5 4 5-4"/></svg>maya@kelvadtrading.com.au</li>
      <li><svg viewBox="0 0 12 12"><circle cx="6" cy="6" r="5"/><path d="M1 6h10M6 1c-2.5 3-2.5 7 0 10M6 1c2.5 3 2.5 7 0 10"/></svg><span><strong>www.heritagehollow</strong>.com.au</span></li>
    </ul>
    <svg class="base-band" viewBox="0 0 588 11" aria-hidden="true">
      <polygon points="0,0 288,0 282,11 0,11" fill="var(--band)"/>
      <polygon points="302,0 588,0 588,11 296,11" fill="var(--band)"/>
    </svg>
  </section>

  <section class="card card--back" aria-label="Business card back">
    <div class="brand-mark">Heritage<br>Hollow</div>
    <div class="web-line">
      <span class="web-line__rule"></span>
      <span class="web-line__url">www.<strong>heritagehollow</strong>.com.au</span>
      <span class="web-line__rule"></span>
    </div>
  </section>
</main>
</body>
</html>
```